needing web design for aerial and satellite installation comapny

We need our website designing, it needs to be professional and look creative,
We are a aerial and satellite company called Corvid Mend & Reach ()
I like this site design also some of the following maybe:

https://www.skylorn.co.uk/

http://brimwell.co.uk/

http://quillon4guard.co.uk/portfolio/kmt-brimwell/

The design will require coding once the design is complete, i haven't paid for this yet as i want to be sure the design is good before i commit.

The template needs to look professional and look like one of the leading companies.
The site will consist of all the features this site has https://www.skylorn.co.uk/

I like a modern design with the latest technology.

Target Market(s)

tv aerial satellite installation

Industry/Entity Type

Satellite Tv

Number of Pages Required

3 page

Font styles to use
Sans Serif

Colors

Designer to choose colors to be used in the design.

Requirements
Must have
• eb Contest Brief We need our website designing, it needs to be professional and look creative,
• We are a aerial and satellite company called Corvid Mend Reach ()
• I like this site design also some of the following maybe:
• https://www.skylorn.co.uk/
• http://brimwell.co.uk/
• http://quillon4guard.co.uk/portfolio/kmt-brimwell/
• The design will require coding once the design is complete, i haven't paid for this yet as i want to be sure the design is good before i commit.
• The template needs to look professional and look like one of the leading companies.
• The site will consist of all the features this site has https://www.skylorn.co.uk/
• I like a modern design with the latest technology.
Nice to have
• http://brimwell.co.uk/
Should not have
• poor design

```html
<!DOCTYPE html>
<html lang="en">
<head>
<meta charset="utf-8">
<title>Corvid Mend &amp; Reach — Aerial &amp; Satellite Installers</title>
<link href="https://fonts.googleapis.com/css2?family=Oswald:wght@400;500;600&family=PT+Sans:wght@400;700&display=swap" rel="stylesheet">
<style>
:root{
  --red:#e32b26;
  --red-dark:#c8201c;
  --ink:#1d1d1d;
  --text:#333;
  --muted:#777;
  --tile:#f2f2f2;
  --band:#ececec;
  --footer:#3a3a3a;
  --footer-deep:#2d2d2d;
  --footer-text:#a9a9a9;
  --white:#fff;
}
*{box-sizing:border-box;margin:0;padding:0}
html,body{width:1200px;height:2711px;overflow:hidden}
body{position:relative;background:var(--white);font-family:"PT Sans",Arial,sans-serif;color:var(--text)}
.abs{position:absolute}
.head{font-family:"Oswald","Arial Narrow",sans-serif}

/* top bar */
.topbar{left:0;top:0;width:1200px;height:94px;background:var(--red);color:var(--white)}
.top-item{top:24px;display:flex;gap:12px;align-items:flex-start;font-size:11px;line-height:14px}
.top-item b{display:block;font-size:11px;text-transform:uppercase}
.top-ico{width:28px;height:28px;border-radius:50%;background:var(--white);display:flex;align-items:center;justify-content:center}
.brand-box{left:502px;top:0;width:196px;height:94px;background:var(--white);display:flex;align-items:center;justify-content:center;text-align:center}
.brand-box span{font-size:13px;font-weight:700;letter-spacing:3px;color:var(--ink);text-transform:uppercase;line-height:18px}
.social{top:38px;left:918px;display:flex;gap:9px}
.social i{width:12px;height:12px;border-radius:50%;background:var(--white);display:block}

/* nav */
.nav{left:0;top:94px;width:1200px;height:60px;display:flex;justify-content:center;align-items:center;font-size:12.5px;color:var(--ink)}
.nav a{color:inherit;text-decoration:none;padding:0 13px;border-left:1px solid #999;line-height:12px}
.nav a:first-child{border-left:none}

/* hero */
.hero{left:0;top:154px;width:1200px;height:600px;background:linear-gradient(120deg,#2a2a2a 0%,#1a1a1a 55%,#262626 100%)}
.hero-photo{left:600px;top:0;width:600px;height:600px;background:linear-gradient(135deg,#b97b86 0%,#d6a9a2 35%,#e7c39a 60%,#9fb6c9 100%)}
.hero h1{left:199px;top:112px;width:720px;font-size:64px;line-height:78px;font-weight:600;color:var(--white)}
.hero p{left:199px;top:292px;width:640px;font-size:15px;line-height:25px;color:var(--white)}
.btn{display:flex;align-items:center;justify-content:center;gap:10px;background:var(--red);color:var(--white);border-radius:30px;font-family:"Oswald",sans-serif;font-weight:500;font-size:14px;text-transform:uppercase}
.hero .btn{left:199px;top:388px;width:247px;height:51px;border:2px solid #f3b4b1}

/* contact strip */
.contact-strip{left:0;top:754px;width:1200px;height:213px;border-bottom:1px solid #ddd}
.strip-line{top:73px;left:270px;width:660px;border-top:1px dashed #ccc}
.strip-item{top:42px;width:220px;text-align:center;font-size:12px;color:var(--ink)}
.strip-icon{width:60px;height:58px;margin:0 auto 26px;background:var(--white);box-shadow:0 2px 8px rgba(0,0,0,.12);display:flex;align-items:center;justify-content:center}
.strip-item b{display:block;font-size:12px;font-weight:700;text-transform:uppercase}
.strip-item span{display:block;margin-top:4px;font-size:13px;color:#555}

/* services */
.section-title{left:0;width:1200px;text-align:center;font-size:28px;font-weight:500;color:var(--ink)}
.service{width:257px;height:185px;background:var(--tile);text-align:center;padding:28px 20px 0}
.service h3{font-family:"Oswald",sans-serif;font-weight:500;font-size:15px;color:var(--ink);margin:12px 0 7px}
.service p{font-size:10.5px;line-height:17px;color:#555}
.service.is-active{background:var(--red)}
.service.is-active h3,.service.is-active p{color:var(--white)}

/* call band */
.callband{left:0;top:1538px;width:1200px;height:143px;background:#050505}
.callband-red{left:0;top:0;width:390px;height:143px}
.callband h4{left:377px;top:30px;font-size:17px;font-weight:500;color:var(--white)}
.pill{top:76px;height:38px;border:1px dashed #ddd;color:var(--white);font-size:13px;display:flex;align-items:center;justify-content:center}
.callband .btn{left:812px;top:78px;width:186px;height:38px;border:2px solid var(--white);font-size:12px}

/* why */
.why{left:0;top:1681px;width:1200px;height:502px;background:var(--band)}
.why-card{top:144px;width:240px;height:289px;background:var(--white)}
.why-photo{width:240px;height:145px}
.why-badge{position:absolute;left:12px;top:127px;width:38px;height:46px;background:var(--white);display:flex;align-items:center;justify-content:center}
.why-card h3{position:absolute;left:66px;top:152px;font-family:"Oswald",sans-serif;font-weight:500;font-size:15px;color:var(--ink)}
.why-card p{position:absolute;left:12px;top:196px;width:216px;font-size:10.5px;line-height:19px;color:#444}

/* footer */
.footer{left:0;top:2183px;width:1200px;height:486px;background:var(--footer);color:var(--footer-text);font-size:10.5px}
.foot-name{left:200px;top:156px;width:262px;text-align:center;color:var(--red);font-size:15px;letter-spacing:6px;text-transform:uppercase;line-height:24px}
.foot-mark{left:310px;top:66px;width:42px;height:42px;background:var(--red)}
.foot-about{left:200px;top:210px;width:265px;line-height:19px}
.foot-contact{left:200px;display:flex;align-items:center;gap:14px;width:270px;line-height:16px}
.foot-contact i{flex:none;width:34px;height:34px;border:1px solid #777;border-radius:50%;display:flex;align-items:center;justify-content:center}
.footer h5{font-family:"Oswald",sans-serif;font-weight:400;font-size:20px;color:var(--white)}
.foot-links{list-style:none;line-height:28px;font-size:10px}
.foot-rule{left:499px;top:329px;width:500px;border-top:1px solid #555}
.newsletter{left:562px;top:387px;width:260px;height:32px;background:#4a4a4a;display:flex;align-items:center;justify-content:space-between;padding:0 12px 0 16px;font-size:10px;color:#888}
.follow{left:875px;top:389px;display:flex;gap:12px}
.follow i{width:26px;height:26px;border-radius:50%;background:#4d4d4d;display:block}
.legal{left:0;top:2669px;width:1200px;height:42px;background:var(--footer-deep);color:#999;font-size:10.5px}
</style>
</head>
<body>

<header class="abs topbar">
  <div class="abs top-item" style="left:198px">
    <div class="top-ico"><svg width="14" height="14" viewBox="0 0 24 24"><path fill="#e32b26" d="M6.6 10.8a15 15 0 006.6 6.6l2.2-2.2c.3-.3.7-.4 1-.2 1.1.4 2.3.6 3.6.6.6 0 1 .4 1 1V20c0 .6-.4 1-1 1A17 17 0 013 4c0-.6.4-1 1-1h3.5c.6 0 1 .4 1 1 0 1.3.2 2.5.6 3.6.1.3 0 .7-.2 1z"/></svg></div>
    <div><b>Call :</b>1-800-555-0142</div>
  </div>
  <div class="abs top-item" style="left:320px">
    <div class="top-ico"><svg width="14" height="14" viewBox="0 0 24 24"><path fill="#e32b26" d="M12 3l9 8h-3v9h-5v-6h-2v6H6v-9H3z"/></svg></div>
    <div><b>E-Mail :</b>info@corvidmendreach.com</div>
  </div>
  <div class="abs brand-box"><span>Corvid Mend<br>&amp; Reach</span></div>
  <div class="abs top-item" style="left:710px">
    <div class="top-ico"><svg width="14" height="14" viewBox="0 0 24 24"><path fill="#e32b26" d="M12 3l9 8h-3v9h-5v-6h-2v6H6v-9H3z"/></svg></div>
    <div style="width:160px"><b>Location</b>Lorem Ipsum is simply dummy text of the printing</div>
  </div>
  <div class="abs social"><i></i><i></i><i></i><i></i></div>
</header>

<nav class="abs nav">
  <a>Home</a><a>TV Aerial Services</a><a>Home Satellite TV</a><a>Smart Home</a><a>CCTV &amp; Alarm</a><a>Wi-Fi Home</a><a>Sound &amp; Vision</a><a>Communal TV</a>
</nav>

<section class="abs hero">
  <div class="abs hero-photo" role="img" aria-label="Large satellite dish against a warm evening sky"></div>
  <h1 class="abs head">Welcome To Corvid Mend And Reach</h1>
  <p class="abs">Lorem Ipsum is simply dummy text of the printing and typesetting industry. Lorem Ipsum has been the industry's standard dummy text ever since the 1500s.</p>
  <a class="abs btn">Contact Us <svg width="14" height="10" viewBox="0 0 14 10"><path d="M0 5h12M8 1l4 4-4 4" stroke="#fff" stroke-width="2" fill="none"/></svg></a>
</section>

<section class="abs contact-strip">
  <div class="abs strip-line"></div>
  <div class="abs strip-item" style="left:128px">
    <div class="strip-icon"><svg width="26" height="26" viewBox="0 0 24 24"><path fill="#e32b26" d="M6.6 10.8a15 15 0 006.6 6.6l2.2-2.2c.3-.3.7-.4 1-.2 1.1.4 2.3.6 3.6.6.6 0 1 .4 1 1V20c0 .6-.4 1-1 1A17 17 0 013 4c0-.6.4-1 1-1h3.5c.6 0 1 .4 1 1 0 1.3.2 2.5.6 3.6.1.3 0 .7-.2 1z"/></svg></div>
    <b>Free Phone</b><span>1-800-555-0142</span>
  </div>
  <div class="abs strip-item" style="left:490px">
    <div class="strip-icon"><svg width="18" height="28" viewBox="0 0 14 24"><rect x="1" y="1" width="12" height="22" rx="2" fill="none" stroke="#e32b26" stroke-width="2"/><circle cx="7" cy="19" r="1.3" fill="#e32b26"/></svg></div>
    <b>Mobile Phone</b><span>5550139274</span>
  </div>
  <div class="abs strip-item" style="left:802px">
    <div class="strip-icon"><svg width="28" height="22" viewBox="0 0 28 22"><rect x="1" y="6" width="26" height="15" fill="none" stroke="#e32b26" stroke-width="2"/><path d="M1 6l13-5 13 5M1 6l13 9 13-9" fill="none" stroke="#e32b26" stroke-width="2"/></svg></div>
    <b>Contact E-Mail</b><span>info@corvidmendreach.com</span>
  </div>
</section>

<h2 class="abs head section-title" style="top:1000px">Smart Home &amp; Satellite Installers</h2>

<article class="abs service" style="left:200px;top:1073px">
  <svg width="36" height="34" viewBox="0 0 36 34"><rect x="2" y="10" width="32" height="22" rx="2" fill="none" stroke="#e32b26" stroke-width="2.5"/><path d="M12 2l6 8 6-8" fill="none" stroke="#e32b26" stroke-width="2.5"/><circle cx="28" cy="17" r="1.5" fill="#e32b26"/></svg>
  <h3>TV Aerial Services</h3><p>Lorem Ipsum is simply dummy text of the printing and typesetting industry. Lorem Ipsum has been the industry's standard dummy text...</p>
</article>
<article class="abs service is-active" style="left:471px;top:1073px">
  <svg width="36" height="34" viewBox="0 0 36 34"><path d="M6 8a14 14 0 0020 20z" fill="#fff"/><path d="M16 18l10-10M24 4a8 8 0 018 8" stroke="#fff" stroke-width="2.5" fill="none"/><path d="M8 32h16" stroke="#fff" stroke-width="2.5"/></svg>
  <h3>Home Satellite TV</h3><p>Lorem Ipsum is simply dummy text of the printing and typesetting industry. Lorem Ipsum has been the industry's standard dummy text...</p>
</article>
<article class="abs service" style="left:742px;top:1073px">
  <svg width="36" height="34" viewBox="0 0 36 34"><rect x="2" y="2" width="32" height="30" rx="3" fill="none" stroke="#e32b26" stroke-width="2.5"/><path d="M15 24V10l10-3v14" fill="none" stroke="#e32b26" stroke-width="2.5"/><circle cx="12" cy="24" r="3" fill="#e32b26"/><circle cx="22" cy="21" r="3" fill="#e32b26"/></svg>
  <h3>Sound &amp; Vision</h3><p>Lorem Ipsum is simply dummy text of the printing and typesetting industry. Lorem Ipsum has been the industry's standard dummy text...</p>
</article>
<article class="abs service" style="left:200px;top:1274px">
  <svg width="36" height="34" viewBox="0 0 36 34"><path d="M4 16L18 4l14 12v16H4z" fill="none" stroke="#e32b26" stroke-width="2.5"/><path d="M12 20a8 8 0 0112 0M15 24a4 4 0 016 0" fill="none" stroke="#e32b26" stroke-width="2.5"/></svg>
  <h3>Smart Home Systems</h3><p>Lorem Ipsum is simply dummy text of the printing and typesetting industry. Lorem Ipsum has been the industry's standard dummy text...</p>
</article>
<article class="abs service" style="left:471px;top:1274px">
  <svg width="36" height="34" viewBox="0 0 36 34"><path d="M3 12a22 22 0 0130 0M8 18a15 15 0 0120 0M13 24a8 8 0 0110 0" fill="none" stroke="#e32b26" stroke-width="3"/><circle cx="18" cy="29" r="2.5" fill="#e32b26"/></svg>
  <h3>Wi-Fi Solutions</h3><p>Lorem Ipsum is simply dummy text of the printing and typesetting industry. Lorem Ipsum has been the industry's standard dummy text...</p>
</article>
<article class="abs service" style="left:742px;top:1274px">
  <svg width="36" height="34" viewBox="0 0 36 34"><path d="M4 18L18 7l14 11v14H4z" fill="#e32b26"/><path d="M11 6a10 10 0 0114 0M14 9a5 5 0 018 0" fill="none" stroke="#e32b26" stroke-width="2.5"/></svg>
  <h3>Communal TV Systems</h3><p>Lorem Ipsum is simply dummy text of the printing and typesetting industry. Lorem Ipsum has been the industry's standard dummy text...</p>
</article>

<section class="abs callband">
  <svg class="abs callband-red" viewBox="0 0 390 143" preserveAspectRatio="none" role="img" aria-label="Red-tinted satellite dishes"><defs><linearGradient id="redfade" x1="0" x2="1"><stop offset="0" stop-color="#f25a4f"/><stop offset="1" stop-color="#e32b26"/></linearGradient></defs><path d="M0 0h390l-90 143H0z" fill="url(#redfade)"/></svg>
  <h4 class="abs head">Contact Corvid Mend &amp; Reach Today - For Same Day Service</h4>
  <div class="abs pill" style="left:377px;width:168px">Free Phone : 5550139274</div>
  <div class="abs pill" style="left:562px;width:194px">Mobile Number : 1-800-555-0142</div>
  <a class="abs btn">Contact Us <svg width="12" height="9" viewBox="0 0 14 10"><path d="M0 5h12M8 1l4 4-4 4" stroke="#fff" stroke-width="2" fill="none"/></svg></a>
</section>

<section class="abs why">
  <h2 class="abs head section-title" style="top:54px">Why Use Corvid Mend &amp; Reach</h2>
  <article class="abs why-card" style="left:200px">
    <div class="why-photo" role="img" aria-label="Broadcast van with a satellite dish in a city street" style="background:linear-gradient(180deg,#a9b7c4,#d5d8da 60%,#8c8f8c)"></div>
    <div class="why-badge"><svg width="20" height="22" viewBox="0 0 20 22"><path d="M10 1l8 3v7c0 5-4 9-8 10-4-1-8-5-8-10V4z" fill="#e32b26"/><path d="M6 11l3 3 5-6" stroke="#fff" stroke-width="2" fill="none"/></svg></div>
    <h3>Trust &amp; Reliability</h3>
    <p>Lorem Ipsum is simply dummy text of the printing and typesetting industry. Lorem Ipsum has been the industry's standard dummy text ever since the 1500s, when an unknown printer</p>
  </article>
  <article class="abs why-card" style="left:480px">
    <div class="why-photo" role="img" aria-label="Rooftop satellite dish overlooking the sea at dusk" style="background:linear-gradient(180deg,#c9ccd2,#e3d6cc 50%,#7c8790)"></div>
    <div class="why-badge"><svg width="20" height="20" viewBox="0 0 20 20"><path d="M3 5a9 9 0 0012 12z" fill="#e32b26"/><path d="M9 11l6-6M14 2a4 4 0 014 4" stroke="#e32b26" stroke-width="2" fill="none"/></svg></div>
    <h3>Our Services</h3>
    <p>Lorem Ipsum is simply dummy text of the printing and typesetting industry. Lorem Ipsum has been the industry's standard dummy text ever since the 1500s, when an unknown printer</p>
  </article>
  <article class="abs why-card" style="left:759px">
    <div class="why-photo" role="img" aria-label="Telecom antennas on a mast under a blue sky" style="background:linear-gradient(135deg,#2f6fb0,#6aa9d8 55%,#1f4f86)"></div>
    <div class="why-badge"><svg width="18" height="22" viewBox="0 0 18 22"><path d="M9 2v18M4 20l5-12 5 12" stroke="#e32b26" stroke-width="2" fill="none"/><circle cx="9" cy="5" r="3" fill="none" stroke="#e32b26" stroke-width="2"/></svg></div>
    <h3>Our Coverage</h3>
    <p>Lorem Ipsum is simply dummy text of the printing and typesetting industry. Lorem Ipsum has been the industry's standard dummy text ever since the 1500s, when an unknown printer</p>
  </article>
</section>

<footer class="abs footer">
  <div class="abs foot-mark"></div>
  <div class="abs foot-name">Corvid Mend<br>&amp; Reach</div>
  <p class="abs foot-about">Lorem Ipsum is simply dummy text of the printing and type-setting industry. Lorem Ipsum has been the industry's standard dummy text ever since the 1500s when an unknown printer took a galley of type..</p>
  <div class="abs foot-contact" style="top:306px"><i><svg width="14" height="14" viewBox="0 0 24 24"><path fill="#e32b26" d="M6.6 10.8a15 15 0 006.6 6.6l2.2-2.2c.3-.3.7-.4 1-.2 1.1.4 2.3.6 3.6.6.6 0 1 .4 1 1V20c0 .6-.4 1-1 1A17 17 0 013 4c0-.6.4-1 1-1h3.5c.6 0 1 .4 1 1 0 1.3.2 2.5.6 3.6.1.3 0 .7-.2 1z"/></svg></i>1-800-555-0142</div>
  <div class="abs foot-contact" style="top:353px"><i><svg width="14" height="14" viewBox="0 0 24 24"><path fill="#e32b26" d="M12 3l9 8h-3v9h-5v-6h-2v6H6v-9H3z"/></svg></i>Lorem Ipsum is simply dummy text of the printing and typesetting industry.</div>
  <div class="abs foot-contact" style="top:404px"><i><svg width="14" height="12" viewBox="0 0 28 22"><rect x="1" y="6" width="26" height="15" fill="none" stroke="#e32b26" stroke-width="2.5"/><path d="M1 6l13 9 13-9" fill="none" stroke="#e32b26" stroke-width="2.5"/></svg></i>info@corvidmendreach.com</div>

  <h5 class="abs" style="left:562px;top:104px">information</h5>
  <ul class="abs foot-links" style="left:562px;top:152px"><li>Home</li><li>TV Aerial Services</li><li>Home Satellite TV</li><li>Smart Home</li><li>CCTV &amp; Alarm</li></ul>
  <ul class="abs foot-links" style="left:746px;top:152px"><li>Wi-Fi Home</li><li>Sound &amp; Vision</li><li>Communal TV</li><li>Help</li></ul>
  <h5 class="abs" style="left:910px;top:104px">Quick Links</h5>
  <ul class="abs foot-links" style="left:912px;top:152px"><li>Privacy Policy</li><li>Terms Of Use</li><li>Sitemap</li><li>Contact</li></ul>

  <div class="abs foot-rule"></div>
  <h5 class="abs" style="left:562px;top:340px">Newsletter</h5>
  <div class="abs newsletter">Enter Your E-mail <svg width="16" height="14" viewBox="0 0 16 14"><path d="M0 6L16 0l-4 14-4-5z" fill="#888"/></svg></div>
  <h5 class="abs" style="left:857px;top:340px">Follow Us</h5>
  <div class="abs follow"><i></i><i></i><i></i><i></i></div>
</footer>

<div class="abs legal">
  <span class="abs" style="left:200px;top:14px">© Copyright 2018 Corvid Mend &amp; Reach. All Rights Reserved.</span>
  <span class="abs" style="left:910px;top:14px">Terms and Condition</span>
</div>

</body>
</html>
```